Tidy paddock Services

After a high quality design website. we are a company that provides services to people that own land and need a hand getting on top of the delayed jobs.
would want a number of tab/ pages for the web page.
Home page / About us page / services page / Gallery page. / Contact us page
we offer a wide range of services .listed below

Stock Work (title)

Stock movement
Break feeding
Temporary staffing

Spraying (title)

Spraying weeds
Spraying gorse

Pastures (title)

Fertilizing
Topping

Building (title)

Habitable sheds
Farm sheds
Sheep yards
Cattle yards
Repair farm buildings
Decks
Retaining walls

Fencing (title)

Stock fencing
Post & rail
Stock yards repair
Electric fencing install & repairs

Water Management (title)

Water trough installation
Water scheme install
Water trough cleaning
Farm water maintenance
Water ponds
Ornamental ponds
Drainage

General (title)

Lawn mowing
Hedge trimming
Pruning trees
Metaling drive ways & races
Water blasting
Small digger work
Little tip truck cartage
Home kill management
Mulching gorse
Section clearing

```html
<!DOCTYPE html>
<html lang="en">
<head>
<meta charset="utf-8">
<title>Tidy paddock Services</title>
<link href="https://fonts.googleapis.com/css2?family=Montserrat:wght@500;600;700;800&family=Lato:wght@400;700&display=swap" rel="stylesheet">
<style>
:root{
  --green:#659a12;
  --green-light:#7fb22a;
  --green-dark:#3e6a0c;
  --ink:#111;
  --text:#333;
  --grey-bg:#f6f6f6;
  --field:#f1f1f1;
  --white:#fff;
}
*{box-sizing:border-box;margin:0;padding:0}
html,body{width:1200px;height:3344px;overflow:hidden;background:var(--white)}
body{position:relative;font-family:"Lato",sans-serif;color:var(--text)}
.abs{position:absolute}
.heading{font-family:"Montserrat",sans-serif;font-weight:700;color:var(--ink)}
.heading span{color:var(--green)}
.btn{position:absolute;display:flex;align-items:center;justify-content:center;border-radius:30px;font-family:"Montserrat",sans-serif;font-weight:700;font-size:17px;letter-spacing:.3px}
.btn-green{background:var(--green);color:var(--white)}

/* hero */
.hero{left:0;top:0;width:1200px;height:780px;overflow:hidden;
  background:
    radial-gradient(ellipse 700px 260px at 600px 330px,rgba(190,200,190,.45),transparent 70%),
    linear-gradient(180deg,#1c2630 0%,#3e4b55 16%,#6f7d83 34%,#8c9690 39%,#3f5a1e 41%,#355d12 50%,#4f8416 64%,#6a9e1c 80%,#5b8e16 100%)}
.brand{left:104px;top:30px;display:flex;align-items:center;gap:10px}
.brand-dot{width:16px;height:16px;border-radius:50%;background:var(--green-light)}
.brand-name{font-family:"Montserrat",sans-serif;font-weight:700;font-size:20px;color:var(--green-light);line-height:1.1;width:200px}
.nav{left:640px;top:41px;display:flex;gap:40px;font-size:16px;color:var(--white)}
.welcome{left:113px;top:278px;font-family:"Montserrat",sans-serif;font-weight:700;font-size:36px;color:var(--green)}
.hero-title{left:113px;top:325px;font-family:"Montserrat",sans-serif;font-weight:700;font-size:72px;color:var(--white);letter-spacing:.5px;white-space:nowrap}
.start{left:118px;top:514px;display:flex;align-items:center;gap:8px;font-family:"Montserrat",sans-serif;font-weight:700;font-size:14px;color:var(--white)}

/* about */
.about-title{left:208px;top:900px;font-size:37px;white-space:nowrap}
.about-text{left:201px;top:962px;width:442px;font-size:15.5px;line-height:25.7px;color:var(--text)}
.about-photo{left:653px;top:898px;width:436px;height:436px;border-radius:50%;
  background:
    radial-gradient(circle at 70% 12%,rgba(250,215,140,.9),transparent 35%),
    radial-gradient(circle at 42% 68%,#6a4e33 0%,#5a4430 28%,transparent 50%),
    linear-gradient(180deg,#c9a66c 0%,#8d8454 22%,#6a7a3a 40%,#4f6a26 62%,#3c5e18 100%)}

/* services */
.services{left:0;top:1443px;width:1200px;height:684px;background:var(--grey-bg)}
.services-title{left:0;top:1512px;width:1200px;text-align:center;font-size:41px}
.card{position:absolute;width:391px;height:152px}
.card-pill{position:absolute;left:64px;top:0;width:327px;height:152px;border:2px solid var(--green);border-radius:76px;background:var(--white)}
.card-photo{position:absolute;left:0;top:8px;width:136px;height:136px;border-radius:50%;z-index:1}
.card-title{position:absolute;left:136px;right:14px;top:0;height:152px;display:flex;align-items:center;justify-content:center;font-family:"Montserrat",sans-serif;font-weight:700;font-size:29px;color:var(--ink)}

/* contact */
.contact{left:0;top:2127px;width:1200px;height:830px;
  background:
    radial-gradient(ellipse 300px 200px at 770px 2340px,rgba(200,210,180,.25),transparent 70%),
    linear-gradient(180deg,#7aa826 0%,#6f9c22 20%,#4f7d16 48%,#5f911c 70%,#79ad2a 100%)}
.contact-title{left:0;top:2184px;width:1143px;text-align:center;font-family:"Montserrat",sans-serif;font-weight:700;font-size:41px;color:var(--white)}
.contact-text{left:296px;top:2257px;width:700px;text-align:center;font-size:15.5px;line-height:26px;color:var(--white)}
.field{position:absolute;height:51px;border-radius:26px;background:var(--field);font-size:15px;color:#8a8a8a;padding:17px 28px}
.submit{left:164px;top:2634px;width:126px;height:52px;background:var(--white);color:var(--green)}
.touch{left:713px;top:2306px;width:487px;height:410px;border-radius:220px 0 0 220px;
  background:
    radial-gradient(ellipse 220px 80px at 280px 60px,rgba(150,60,60,.35),transparent 70%),
    linear-gradient(160deg,#3b3430 0%,#33391f 40%,#2f4a14 75%,#47731a 100%)}
.touch-title{left:812px;top:2370px;font-family:"Montserrat",sans-serif;font-weight:700;font-size:29px;color:var(--white)}
.touch-item{position:absolute;left:817px;display:flex;gap:14px;font-size:15.5px;line-height:26px;color:var(--white)}
.touch-item svg{flex:none;margin-top:4px}
.social{position:absolute;display:flex;gap:10px}
.social i{display:block;width:41px;height:41px;border-radius:50%}

/* footer */
.footer-brand{left:0;top:3012px;width:1200px;display:flex;align-items:center;justify-content:center;gap:16px}
.footer-dot{width:30px;height:30px;border-radius:50%;background:var(--green)}
.footer-name{font-family:"Montserrat",sans-serif;font-weight:700;font-size:42px;line-height:1.1;color:var(--green)}
.footer-links{left:0;top:3143px;width:1200px;text-align:center;font-size:15px;color:#222}
.footer-links b{font-weight:400;margin:0 16px}
.copyright{left:0;top:3193px;width:1200px;text-align:center;font-size:15.5px;color:#222}
.copyright u{text-decoration:underline}
</style>
</head>
<body>

<!-- hero -->
<section class="abs hero" role="img" aria-label="Photo of green crop rows stretching to the horizon under a dusky sky"></section>
<svg class="abs" style="left:0;top:420px" width="1200" height="370" viewBox="0 420 1200 370" aria-hidden="true">
  <path d="M0,592 Q560,974 1200,440 L1200,790 L0,790 Z" fill="var(--green)"/>
  <path d="M0,600 Q560,997 1200,470 L1200,790 L0,790 Z" fill="var(--white)"/>
</svg>
<div class="abs brand"><span class="brand-dot"></span><span class="brand-name">TIDY PADDOCK SERVICES</span></div>
<nav class="abs nav"><span>Home</span><span>About Us</span><span>Services</span><span>Gallery</span><span>Contact Us</span></nav>
<div class="abs welcome">WELCOME TO</div>
<h1 class="abs hero-title">TIDY PADDOCK SERVICES</h1>
<div class="abs start">
  <svg width="44" height="48" viewBox="0 0 44 48" aria-hidden="true">
    <circle cx="22" cy="24" r="20" fill="none" stroke="var(--white)" stroke-width="1.5"/>
    <path d="M15,24 H29 M24,19 L29,24 L24,29" fill="none" stroke="var(--green-light)" stroke-width="2"/>
  </svg>
  <span>GET STARTED</span>
</div>

<!-- about -->
<svg class="abs" style="left:0;top:840px" width="1200" height="400" viewBox="0 840 1200 400" aria-hidden="true">
  <path d="M800,908 Q775,862 720,862 L300,862 C185,862 123,950 123,1037 C123,1110 160,1158 200,1182" fill="none" stroke="var(--green)" stroke-width="2.5"/>
  <path d="M380,1213 L690,1213" fill="none" stroke="var(--green)" stroke-width="2.5"/>
</svg>
<h2 class="abs heading about-title">ABOUT <span>TIDY PADDOCK</span></h2>
<p class="abs about-text">Lorem ipsum dolor sit amet, consectetur adipiscing elit, sed do eiusmod tempor incididunt ut labore et dolore magna aliqua. Quis ipsum suspendisse ultrices gravida. Risus commodo viverra maecenas accumsan lacus vel facilisis. Lorem ipsum dolor sit amet, consectetur adipiscing elit, sed do eiusmod tempor incididunt ut labore et dolore magna aliqua. Quis ipsum suspendisse ultrices gravida. Risus commodo viverra maecenas accumsan lacus vel facilisis.</p>
<div class="btn btn-green" style="left:197px;top:1182px;width:184px;height:53px">LEARN MORE</div>
<div class="abs about-photo" role="img" aria-label="Circular collage of farmers in a field at sunset and hands holding a seedling in soil"></div>

<!-- services -->
<section class="abs services"></section>
<h2 class="abs heading services-title">OUR <span>SERVICES</span></h2>
<div class="card" style="left:170px;top:1600px">
  <div class="card-pill"></div>
  <div class="card-photo" role="img" aria-label="Farmer checking young crops" style="background:linear-gradient(160deg,#2c3424 0%,#3e5424 40%,#6f9a34 70%,#2f4a18 100%)"></div>
  <div class="card-title">Stock Work</div>
</div>
<div class="card" style="left:629px;top:1600px">
  <div class="card-pill"></div>
  <div class="card-photo" role="img" aria-label="Tractor spraying a green field" style="background:linear-gradient(180deg,#5f86a6 0%,#b7cad4 38%,#6f8f4a 48%,#3f6d1a 70%,#2c4f10 100%)"></div>
  <div class="card-title">Spraying</div>
</div>
<div class="card" style="left:170px;top:1790px">
  <div class="card-pill"></div>
  <div class="card-photo" role="img" aria-label="Sheep grazing a hillside pasture at sunrise" style="background:radial-gradient(circle at 62% 30%,#f4d48a 0%,transparent 25%),linear-gradient(180deg,#8fa0a6 0%,#a69a6a 30%,#5d7a2c 55%,#4a6a20 80%,#8c8c78 100%)"></div>
  <div class="card-title">Pastures</div>
</div>
<div class="card" style="left:629px;top:1790px">
  <div class="card-pill"></div>
  <div class="card-photo" role="img" aria-label="Large greenhouse building beside crop rows" style="background:linear-gradient(180deg,#8fb0c6 0%,#d6dee0 38%,#9aa29a 50%,#4f7424 66%,#2f5212 100%)"></div>
  <div class="card-title">Building</div>
</div>
<div class="btn btn-green" style="left:508px;top:1981px;width:185px;height:53px">VIEW MORE</div>

<!-- contact -->
<section class="abs contact" role="img" aria-label="Soft focus photo of a green crop field with a sprayer in the distance"></section>
<h2 class="abs contact-title">CONTACT US</h2>
<p class="abs contact-text">Lorem ipsum dolor sit amet, consectetur adipiscing elit, sed do eiusmod tempor incididunt ut labore et dolore magna aliqua. Quis ipsum suspendisse ultrices gravida.</p>
<div class="field" style="left:157px;top:2341px;width:255px">First Name</div>
<div class="field" style="left:430px;top:2341px;width:255px">Late Name</div>
<div class="field" style="left:157px;top:2409px;width:255px">Email</div>
<div class="field" style="left:430px;top:2409px;width:254px">Phone</div>
<div class="field" style="left:157px;top:2477px;width:526px;height:141px;border-radius:34px">Messages</div>
<div class="btn submit">SUBMIT</div>

<div class="abs touch" role="img" aria-label="Dark photo of a tractor sprayer working in a field"></div>
<div class="abs touch-title">GET IN TOUCH</div>
<div class="touch-item" style="top:2428px">
  <svg width="16" height="20" viewBox="0 0 16 20" aria-hidden="true"><path d="M8,0 C3.6,0 0,3.4 0,7.6 C0,13 8,20 8,20 C8,20 16,13 16,7.6 C16,3.4 12.4,0 8,0 Z" fill="var(--green-light)"/><circle cx="8" cy="7.5" r="3" fill="#2f3a1a"/></svg>
  <span style="width:290px">12 At Home dolor sit amet, consectetur adipiscing elit</span>
</div>
<div class="touch-item" style="top:2505px">
  <svg width="18" height="18" viewBox="0 0 24 24" aria-hidden="true"><path d="M6.6,10.8 C8,13.6 10.4,16 13.2,17.4 L15.4,15.2 C15.7,14.9 16.1,14.8 16.4,15 C17.5,15.4 18.7,15.6 20,15.6 C20.6,15.6 21,16 21,16.6 V20 C21,20.6 20.6,21 20,21 C10.6,21 3,13.4 3,4 C3,3.4 3.4,3 4,3 H7.5 C8.1,3 8.5,3.4 8.5,4 C8.5,5.3 8.7,6.5 9.1,7.6 C9.2,7.9 9.1,8.3 8.9,8.6 Z" fill="var(--green-light)"/></svg>
  <span>+1 555 010 2040</span>
</div>
<div class="touch-item" style="top:2554px">
  <svg width="18" height="16" viewBox="0 0 18 14" aria-hidden="true"><rect x="0" y="0" width="18" height="14" rx="2" fill="var(--green-light)"/><path d="M1,1.5 L9,8 L17,1.5" fill="none" stroke="#2f3a1a" stroke-width="1.5"/></svg>
  <span>hello@tidypaddock.example</span>
</div>
<div class="social" style="left:814px;top:2610px">
  <i style="background:var(--green-light)"></i>
  <i style="border:1.5px solid var(--green-light)"></i>
  <i style="border:1.5px solid var(--green-light)"></i>
  <i style="border:1.5px solid var(--green-light)"></i>
</div>

<!-- footer -->
<svg class="abs" style="left:0;top:2780px" width="1200" height="180" viewBox="0 2780 1200 180" aria-hidden="true">
  <path d="M0,2948 Q600,2682 1200,2948 L1200,2960 L0,2960 Z" fill="var(--white)"/>
  <path d="M130,2907 Q600,2660 1045,2905 Q600,2700 130,2907 Z" fill="var(--green)"/>
</svg>
<div class="abs footer-brand"><span class="footer-dot"></span><span class="footer-name">Tidy paddock Services</span></div>
<div class="abs footer-links">Terms &amp; conditions<b>|</b>Privacy Policy<b>|</b>About Us Support</div>
<div class="abs copyright">©Copyrights 2024 <u>Tidy paddock Services.</u> &nbsp;| &nbsp; All Rights Reserved</div>
<div class="social" style="left:500px;top:3245px;gap:9px">
  <i style="width:44px;height:44px;background:var(--green)"></i>
  <i style="width:44px;height:44px;background:#efefef"></i>
  <i style="width:44px;height:44px;background:#efefef"></i>
  <i style="width:44px;height:44px;background:#efefef"></i>
</div>

</body>
</html>
```